Profesional personal website needs design and business card

I need a business card with my professional name as a logo "Dorian Vitality" for my business. I am a Wellness Coach, consultant and trainer. So it should be professional, wellness oriented and modern.

Target Market(s)

Private clients, governments, corporations. Luxury and high market.

Industry/Entity Type

Health And Wellness

Contact Information for Business Card

Dorian Vitality should be the logo

Colors

Designer to choose colors to be used in the design.

Requirements
Must have
• Dorian Vitality
• Name: Tomás Lirandel
• Wellness Coach, Consultant & Trainer.
• Website: www.dorianvitality-example.com
• Phone:
• Spain (+34) 612 480 317
• (USA) +1 (555) 610 4829
Nice to have
• The most important is the design of "Dorian Vitality", as this is going to be my personal brand logo. It should be professional, wellness, high end and actual.
Should not have
• no golds, no baroque style..

```html
<!DOCTYPE html>
<html lang="en">
<head>
<meta charset="UTF-8">
<title>Dorian Vitality — Business Card</title>
<link href="https://fonts.googleapis.com/css2?family=Oswald:wght@400;500&display=swap" rel="stylesheet">
<style>
  :root {
    --green: #00a332;
    --orange: #f58200;
    --paper: #f3f4f7;
    --white: #ffffff;
    --backdrop: #e8e5e0;
  }
  * { margin: 0; padding: 0; box-sizing: border-box; }
  html, body { width: 1200px; height: 800px; overflow: hidden; }
  body {
    background: var(--backdrop);
    font-family: "Oswald", "Arial Narrow", sans-serif;
    position: relative;
  }
  .card {
    position: absolute;
    left: 290px;
    width: 620px;
    height: 354px;
    overflow: hidden;
    box-shadow: 0 6px 18px rgba(0,0,0,0.18);
  }
  .card--front { top: 28px; background: var(--green); }
  .card--back { top: 418px; background: var(--paper); }

  .brand-name {
    position: absolute;
    font-weight: 500;
    white-space: nowrap;
    letter-spacing: 0.5px;
  }
  .card--front .brand-name {
    color: var(--white);
    font-size: 58px;
    left: 0; right: 0; top: 50%;
    transform: translateY(-50%);
    text-align: center;
  }
  .card--back .brand-name {
    color: var(--green);
    font-size: 46px;
    left: 30px;
    bottom: 38px;
  }

  .contact-panel {
    position: absolute;
    left: 392px; top: 0;
    width: 228px; height: 100%;
    background: var(--green);
  }

  .person {
    position: absolute;
    right: 248px;
    top: 56px;
    text-align: right;
  }
  .person__name {
    color: var(--orange);
    font-size: 30px;
    font-weight: 500;
    line-height: 1.1;
  }
  .person__role {
    color: var(--green);
    font-size: 14px;
    font-weight: 500;
    line-height: 1.3;
  }
  .person__rule {
    width: 92px;
    height: 3px;
    background: var(--orange);
    margin: 6px 6px 0 auto;
  }

  .icon-tab {
    position: absolute;
    left: 362px; top: 140px;
    width: 56px; height: 176px;
    background: var(--orange);
    border: 4px solid var(--white);
    border-radius: 16px;
    display: flex;
    flex-direction: column;
    align-items: center;
    justify-content: space-around;
    padding: 14px 0;
  }
  .icon-tab svg { width: 22px; height: 22px; }

  .contact-list {
    position: absolute;
    left: 440px; top: 160px;
    list-style: none;
    color: var(--white);
    font-size: 13px;
    font-weight: 400;
    letter-spacing: 1px;
    line-height: 1.35;
  }
  .contact-list li { margin-bottom: 28px; }
  .contact-list li:first-child { margin-bottom: 22px; }
</style>
</head>
<body>
  <section class="card card--front">
    <span class="brand-name">Dorian Vitality</span>
  </section>

  <section class="card card--back">
    <div class="contact-panel"></div>

    <div class="person">
      <p class="person__name">Tomás Lirandel</p>
      <p class="person__role">Wellness Coach, Consultant &amp; Trainer</p>
      <div class="person__rule"></div>
    </div>

    <div class="icon-tab">
      <svg viewBox="0 0 24 24" aria-label="Phone">
        <path fill="#fff" d="M6.6 10.8c1.4 2.8 3.8 5.1 6.6 6.6l2.2-2.2c.3-.3.7-.4 1-.2 1.1.4 2.3.6 3.6.6.6 0 1 .4 1 1V20c0 .6-.4 1-1 1C10.6 21 3 13.4 3 4c0-.6.4-1 1-1h3.5c.6 0 1 .4 1 1 0 1.3.2 2.5.6 3.6.1.3 0 .7-.2 1z"/>
      </svg>
      <svg viewBox="0 0 24 24" aria-label="Email">
        <rect x="2.5" y="5.5" width="19" height="13" fill="none" stroke="#fff" stroke-width="1.8"/>
        <polyline points="2.5,5.5 12,13 21.5,5.5" fill="none" stroke="#fff" stroke-width="1.8"/>
        <polyline points="2.5,18.5 9.5,11.5 M14.5,11.5 21.5,18.5" fill="none" stroke="#fff" stroke-width="1.4"/>
      </svg>
      <svg viewBox="0 0 24 24" aria-label="Website">
        <circle cx="12" cy="12" r="9" fill="none" stroke="#fff" stroke-width="1.8"/>
        <ellipse cx="12" cy="12" rx="4" ry="9" fill="none" stroke="#fff" stroke-width="1.5"/>
        <line x1="3" y1="12" x2="21" y2="12" stroke="#fff" stroke-width="1.5"/>
        <line x1="4.5" y1="7.5" x2="19.5" y2="7.5" stroke="#fff" stroke-width="1.3"/>
        <line x1="4.5" y1="16.5" x2="19.5" y2="16.5" stroke="#fff" stroke-width="1.3"/>
      </svg>
    </div>

    <ul class="contact-list">
      <li>Spain (+34) 612 480 317<br>(USA) +1 (555) 610 4829</li>
      <li>hello@dorianvitality-example.com</li>
      <li>www.dorianvitality-example.com</li>
    </ul>

    <span class="brand-name">Dorian Vitality</span>
  </section>
</body>
</html>
```